Audio and Video download site

I am looking for a good and beautiful website where users can be a able to download and upload musicial files and video file. Basically, there will be two categories. The first category for the music files( mp3, mva and other popular music files) while the second category will be for video files (mp4, wmv, divx and other files) users would be able to like and dislike a song/video. Users do not necessarily have to sign up for them to make you or download and upload files from the website. The website should be youthful.

```html
<!DOCTYPE html>
<html lang="en">
<head>
<meta charset="utf-8">
<title>Tunora — Music &amp; Video Downloads</title>
<link rel="stylesheet" href="https://fonts.googleapis.com/css2?family=Open+Sans:ital,wght@0,400;0,600;0,700;1,400;1,600&family=Lora:wght@400;700&display=swap">
<style>
:root{
  --navy:#232b3a;
  --navy-deep:#1f2734;
  --orange:#f47a2f;
  --blue:#1a8fd1;
  --ink:#1f1f1f;
  --muted:#8a8f96;
  --line:#e6e6e6;
  --soft:#eeeeee;
  --chip:#6f6f6f;
  --white:#ffffff;
}
*{box-sizing:border-box;margin:0;padding:0}
html,body{width:1200px;height:2442px;overflow:hidden}
body{font-family:"Open Sans",Arial,sans-serif;color:var(--ink);background:var(--white);position:relative}
a{color:inherit;text-decoration:none}
svg.ico{display:inline-block;vertical-align:middle;fill:currentColor}

/* header */
.site-header{height:73px;background:var(--navy);position:relative}
.brand{position:absolute;left:98px;top:18px;color:var(--white);font-size:26px;font-weight:600;letter-spacing:.3px}
.main-nav{position:absolute;top:28px;left:430px;display:flex;font-size:12px;color:#c7ccd4}
.main-nav a:nth-child(1){position:absolute;left:16px;color:var(--orange)}
.main-nav a:nth-child(2){position:absolute;left:92px}
.main-nav a:nth-child(3){position:absolute;left:167px}
.main-nav a:nth-child(4){position:absolute;left:240px;white-space:nowrap}
.main-nav a:nth-child(5){position:absolute;left:309px}
.main-nav a:nth-child(6){position:absolute;left:377px}
.header-btn{position:absolute;top:24px;height:25px;border-radius:13px;color:var(--white);font-size:12px;font-weight:600;line-height:25px;text-align:center}
.btn-login{left:874px;width:124px;background:var(--orange)}
.btn-upload{left:1003px;width:97px;background:var(--blue)}

/* hero */
.hero{position:absolute;left:98px;top:96px;width:716px;height:405px;background:linear-gradient(100deg,#3b2f2a 0%,#6e5a4c 35%,#b7aa9c 65%,#e8e4de 100%);overflow:hidden}
.hero-photo{position:absolute;inset:0}
.hero-arrow{position:absolute;left:36px;top:194px;width:16px;height:28px;color:rgba(255,255,255,.8)}
.hero-copy{position:absolute;left:70px;top:214px;width:420px;color:var(--white)}
.tag{display:inline-block;background:var(--blue);font-size:8px;font-weight:700;letter-spacing:1px;padding:3px 10px}
.hero-title{font-family:"Lora",Georgia,serif;font-weight:700;font-size:25px;margin-top:7px}
.hero-text{font-family:"Lora",Georgia,serif;font-size:12.5px;line-height:20px;margin-top:8px}
.btn-ghost{display:inline-block;margin-top:18px;border:1.5px solid var(--white);border-radius:14px;font-size:11px;letter-spacing:2.5px;padding:4px 15px;font-weight:600}

/* categories */
.categories{position:absolute;left:838px;top:96px;width:262px;height:405px;background:var(--navy)}
.categories h2{height:57px;background:var(--blue);color:var(--white);font-size:20px;font-weight:600;text-align:center;line-height:57px}
.cat-tabs{display:flex;height:43px;margin:0 20px;position:relative}
.cat-tabs span{flex:1;text-align:center;color:var(--white);font-size:15px;line-height:42px}
.cat-tabs span:first-child{border-bottom:2px solid var(--orange)}
.cat-tabs::after{content:"";position:absolute;left:50%;top:10px;height:24px;border-left:1px solid #55606f}
.cat-list{list-style:none;margin:22px 20px 0 24px}
.cat-list li{height:34px;border-bottom:1px solid #333d4d;color:var(--white);font-size:11px;display:flex;align-items:center;text-transform:uppercase}
.cat-list li svg{width:12px;height:12px;margin-right:20px}
.cat-more{position:absolute;right:20px;bottom:16px;color:var(--white);font-size:11px;display:flex;align-items:center;gap:5px}

/* search */
.search-bar{position:absolute;left:98px;top:545px;width:716px;height:67px;background:var(--soft)}
.field{position:absolute;top:17px;height:33px;background:var(--white);font-size:11px;color:#777;padding:0 13px;line-height:33px}
.field-keyword{left:16px;width:215px}
.field-category{left:241px;width:213px}
.field-category svg{position:absolute;right:12px;top:12px;width:10px;height:10px}
.btn-search{position:absolute;left:487px;top:17px;width:213px;height:33px;background:var(--orange);color:var(--white);font-size:14px;font-weight:600;text-align:center;line-height:33px}

/* media sections */
.media-section{position:absolute;left:98px;width:716px}
.section-music{top:654px}
.section-video{top:1386px}
.section-head{display:flex;justify-content:space-between;align-items:center;height:36px}
.section-head h2{font-size:24px;font-weight:600}
.view-all{font-size:11px;font-weight:600;display:flex;align-items:center;gap:6px;margin-right:4px}
.grid{display:grid;grid-template-columns:repeat(3,225px);column-gap:20px;row-gap:35px;margin-top:30px}
.card-media{height:158px;position:relative}
.play{position:absolute;left:50%;top:50%;width:34px;height:34px;margin:-17px 0 0 -17px;border:2px solid rgba(255,255,255,.75);border-radius:50%}
.play::after{content:"";position:absolute;left:12px;top:8px;border-left:11px solid rgba(255,255,255,.8);border-top:7px solid transparent;border-bottom:7px solid transparent}
.card-title{font-size:14px;font-weight:600;line-height:21px;margin-top:15px}
.card-meta{display:flex;justify-content:space-between;align-items:center;margin-top:7px;font-size:8.5px;font-style:italic}
.card-meta b{font-weight:700}
.count{background:var(--chip);color:var(--white);font-style:normal;font-size:8.5px;font-weight:600;padding:1px 4px;position:relative}
.count::after{content:"";position:absolute;right:0;bottom:-4px;border-top:4px solid var(--chip);border-left:4px solid transparent}
.card-actions{display:flex;align-items:center;height:32px;background:#f0f0f0;margin-top:13px;padding:0 10px;font-size:10.5px}
.card-actions svg{width:12px;height:12px;margin-right:4px}
.card-actions .dislike{margin-left:18px}
.card-actions .dl{margin-left:auto}
.section-rule{position:absolute;left:98px;top:1368px;width:716px;border-top:1px solid var(--line)}

/* sidebar */
.sidebar{position:absolute;left:838px;top:545px;width:262px;height:1523px;border:1px solid var(--line);border-right:none}
.side-block{border-bottom:1px solid var(--line);padding:0 0 0 33px;position:relative}
.subscribe{height:217px;padding-top:24px}
.side-title{font-size:14px;font-weight:600}
.side-text{font-size:11px;color:var(--muted);line-height:18px;margin-top:4px;width:200px}
.input-email{width:208px;height:34px;border:1px solid #d8d8d8;margin-top:12px;font-size:11px;color:#999;display:flex;align-items:center;padding-left:12px}
.input-email svg{width:12px;height:10px;margin-right:10px;color:#bbb}
.btn-send{width:128px;height:32px;background:#cfcfcf;color:var(--white);font-size:11px;text-align:center;line-height:32px;margin-top:15px;border-bottom:2px solid #bdbdbd}
.topics{height:244px;list-style:none;padding-top:29px}
.topics li{display:flex;align-items:center;height:32.5px;font-size:11px;color:#333}
.topics li svg{width:13px;height:13px;margin-right:17px;color:#333}
.gallery{height:528px;padding-top:28px;padding-left:28px}
.thumb{width:200px;height:136px}
.thumb-2{margin-left:8px;width:193px;height:94px;margin-top:20px}
.thumb-3{margin-left:8px;width:193px;height:93px;margin-top:20px}
.caption{font-size:11px;color:#a3a7ad;line-height:17px;width:200px;margin-left:8px;margin-top:3px}
.services{height:355px;padding-top:30px}
.service{display:flex;align-items:center;margin-top:20px}
.service:first-of-type{margin-top:22px}
.svc-icon{width:60px;height:60px;border:1px solid #c9e4f4;border-radius:50%;display:flex;align-items:center;justify-content:center;color:var(--orange);flex:none}
.svc-icon svg{width:22px;height:22px}
.service p{font-size:11px;color:var(--muted);line-height:18px;margin-left:16px;width:150px}
.about{border-bottom:none;padding-top:30px}
.about p{font-size:11px;color:#555;line-height:18px;margin-top:12px;width:220px}
.about a{color:var(--blue)}

/* footer */
.site-footer{position:absolute;left:0;top:2162px;width:1200px;height:280px;background:var(--navy)}
.foot-col{position:absolute;top:40px;color:var(--white)}
.foot-col h3{font-size:11px;font-weight:700;letter-spacing:.3px}
.col-connect{left:98px}
.col-mail{left:535px}
.col-menu{left:955px}
.foot-divider{position:absolute;top:26px;height:195px;border-left:1px solid #394355}
.social{display:flex;gap:6px;margin-top:34px}
.social-tile{width:73px;height:93px;color:var(--white);text-align:center;font-size:12px;padding-top:14px}
.social-tile .dot{display:block;width:34px;height:34px;margin:0 auto;border-radius:50%;background:rgba(0,0,0,.15);font-size:8px;font-weight:600;line-height:34px}
.social-tile .num{display:block;margin-top:16px}
.t-friends{background:#3b5a99}
.t-chirps{background:#2aa3e0}
.t-circles{background:#e04a35}
.col-mail p{font-size:11px;line-height:20px;margin-top:25px;width:240px}
.mail-form{display:flex;margin-top:14px}
.mail-input{width:198px;height:26px;background:var(--white);font-size:10px;color:#999;line-height:26px;padding-left:10px}
.mail-btn{width:34px;height:26px;background:var(--orange);display:flex;align-items:center;justify-content:center;color:var(--white)}
.mail-btn svg{width:12px;height:12px}
.privacy{font-size:10px;margin-top:10px}
.foot-menu{list-style:none;margin-top:30px;font-size:10.5px}
.foot-menu li{height:21px}
.copyright{position:absolute;left:0;right:0;top:252px;text-align:center;color:var(--white);font-size:10px}
</style>
</head>
<body>

<svg width="0" height="0" style="position:absolute" aria-hidden="true">
  <defs>
    <symbol id="i-note" viewBox="0 0 16 16"><path d="M5 2l10-2v11.5a2.5 2.5 0 1 1-2-2.45V3.6L7 4.8v8.7A2.5 2.5 0 1 1 5 11z"/></symbol>
    <symbol id="i-up" viewBox="0 0 16 16"><path d="M1 7h3v8H1zM5 15V7l4-6c1.2 0 2 .8 2 2l-.6 3H15c.6 0 1 .5 1 1l-1.6 7c-.2.6-.6 1-1.2 1z"/></symbol>
    <symbol id="i-down" viewBox="0 0 16 16"><path d="M1 1h3v8H1zM5 1v8l4 6c1.2 0 2-.8 2-2l-.6-3H15c.6 0 1-.5 1-1L14.4 2c-.2-.6-.6-1-1.2-1z"/></symbol>
    <symbol id="i-dl" viewBox="0 0 16 16"><path d="M6 1h4v6h3l-5 5-5-5h3zM1 13h14v2H1z"/></symbol>
    <symbol id="i-circle-arrow" viewBox="0 0 16 16"><circle cx="8" cy="8" r="7" fill="none" stroke="currentColor" stroke-width="1.3"/><path d="M6.5 4.5L10 8l-3.5 3.5" fill="none" stroke="currentColor" stroke-width="1.4"/></symbol>
    <symbol id="i-send" viewBox="0 0 16 16"><path d="M0 7l16-7-5 16-3-6z"/></symbol>
    <symbol id="i-heart" viewBox="0 0 16 16"><path d="M8 15L1.5 8.5A4 4 0 0 1 8 3a4 4 0 0 1 6.5 5.5z"/></symbol>
    <symbol id="i-globe" viewBox="0 0 16 16"><circle cx="8" cy="8" r="7" fill="none" stroke="currentColor" stroke-width="1.5"/><path d="M1 8h14M8 1c-3 3-3 11 0 14M8 1c3 3 3 11 0 14" fill="none" stroke="currentColor" stroke-width="1.2"/></symbol>
    <symbol id="i-mouse" viewBox="0 0 16 16"><rect x="4" y="1" width="8" height="14" rx="4" fill="none" stroke="currentColor" stroke-width="1.5"/><path d="M8 3v4" stroke="currentColor" stroke-width="1.5"/></symbol>
    <symbol id="i-video" viewBox="0 0 16 16"><rect x="0" y="4" width="11" height="9" rx="1.5"/><path d="M11 8l5-3v8l-5-3z"/></symbol>
    <symbol id="i-cart" viewBox="0 0 16 16"><path d="M0 1h3l2.2 8.5h8.3L16 3H4.3" fill="none" stroke="currentColor" stroke-width="1.6"/><circle cx="6" cy="13.5" r="1.5"/><circle cx="13" cy="13.5" r="1.5"/></symbol>
    <symbol id="i-mail" viewBox="0 0 16 12"><path d="M0 0h16v12H0zM1 1l7 6 7-6"/></symbol>
    <symbol id="i-check" viewBox="0 0 16 16"><path d="M1 8l4 4 10-10" fill="none" stroke="currentColor" stroke-width="2.5"/></symbol>
    <symbol id="i-caret" viewBox="0 0 10 10"><path d="M1 3l4 4 4-4" fill="none" stroke="currentColor" stroke-width="1.3"/></symbol>
  </defs>
</svg>

<header class="site-header">
  <a class="brand" href="#">Tunora</a>
  <nav class="main-nav">
    <a href="#">Home</a><a href="#">Features</a><a href="#">About</a><a href="#">Meet us</a><a href="#">Blog</a><a href="#">Contact</a>
  </nav>
  <a class="header-btn btn-login" href="#">Login / Sign Up</a>
  <a class="header-btn btn-upload" href="#">Upload Now</a>
</header>

<section class="hero">
  <div class="hero-photo" role="img" aria-label="Young woman singing joyfully into a microphone"></div>
  <svg class="hero-arrow" viewBox="0 0 16 28"><path d="M14 2L3 14l11 12" fill="none" stroke="currentColor" stroke-width="2"/></svg>
  <div class="hero-copy">
    <span class="tag">LIVESTYLE</span>
    <h1 class="hero-title">Lorem Ipsum Dolor</h1>
    <p class="hero-text">For many it means that you're no longer in the hard-partying, bad decision-making stage of your life, for better or for worse.</p>
    <a class="btn-ghost" href="#">READ MORE</a>
  </div>
</section>

<aside class="categories">
  <h2>Categories</h2>
  <div class="cat-tabs"><span>Music</span><span>Videos</span></div>
  <ul class="cat-list">
    <li><svg class="ico"><use href="#i-note"/></svg>MP3</li>
    <li><svg class="ico"><use href="#i-note"/></svg>MVA</li>
    <li><svg class="ico"><use href="#i-note"/></svg>FLAC</li>
    <li><svg class="ico"><use href="#i-note"/></svg>Marmot Audio</li>
    <li><svg class="ico"><use href="#i-note"/></svg>Wavefold</li>
    <li><svg class="ico"><use href="#i-note"/></svg>WV</li>
    <li><svg class="ico"><use href="#i-note"/></svg>TTA</li>
  </ul>
  <a class="cat-more" href="#">MORE <svg class="ico" width="11" height="11"><use href="#i-circle-arrow"/></svg></a>
</aside>

<form class="search-bar">
  <div class="field field-keyword">Keyword</div>
  <div class="field field-category">Category<svg class="ico"><use href="#i-caret"/></svg></div>
  <div class="btn-search">SEARCH</div>
</form>

<section class="media-section section-music">
  <div class="section-head"><h2>Latest Music’s</h2><a class="view-all" href="#">View All <svg class="ico" width="12" height="12"><use href="#i-circle-arrow"/></svg></a></div>
  <div class="grid">
    <article class="card"><div class="card-media" role="img" aria-label="Concert crowd silhouettes against golden stage lights" style="background:linear-gradient(160deg,#6b5a1e,#d8b84a 45%,#2a2414)"></div>
      <h3 class="card-title">Lorem ipsum dolor sit am onse adipiscing elit</h3>
      <div class="card-meta"><span><b>Mara Kell</b> - Jul 23, 2016</span><span class="count">57</span></div>
      <div class="card-actions"><svg class="ico"><use href="#i-up"/></svg>22<span class="dislike"><svg class="ico"><use href="#i-down"/></svg>4</span><span class="dl"><svg class="ico"><use href="#i-dl"/></svg>Download</span></div></article>
    <article class="card"><div class="card-media" role="img" aria-label="Woman with headphones amid colourful paint splashes" style="background:linear-gradient(135deg,#3aa5c9,#e6c14a 40%,#c44a8a 70%,#4a8bd0)"><span class="play"></span></div>
      <h3 class="card-title">Lorem ipsum dolor sit am onse adipiscing elit</h3>
      <div class="card-meta"><span><b>Mara Kell</b> - Jul 23, 2016</span><span class="count">57</span></div>
      <div class="card-actions"><svg class="ico"><use href="#i-up"/></svg>22<span class="dislike"><svg class="ico"><use href="#i-down"/></svg>4</span><span class="dl"><svg class="ico"><use href="#i-dl"/></svg>Download</span></div></article>
    <article class="card"><div class="card-media" role="img" aria-label="Festival crowd with raised hands under blue sky" style="background:linear-gradient(180deg,#9fc4e0,#d9c3a6 45%,#7a4a3a)"></div>
      <h3 class="card-title">Lorem ipsum dolor sit am onse adipiscing elit</h3>
      <div class="card-meta"><span><b>Mara Kell</b> - Jul 23, 2016</span><span class="count">57</span></div>
      <div class="card-actions"><svg class="ico"><use href="#i-up"/></svg>22<span class="dislike"><svg class="ico"><use href="#i-down"/></svg>4</span><span class="dl"><svg class="ico"><use href="#i-dl"/></svg>Download</span></div></article>
    <article class="card"><div class="card-media" role="img" aria-label="Dancer with hair flying in dark ink splash" style="background:linear-gradient(150deg,#a27cb8,#3c2a44 55%,#b89ac4)"></div>
      <h3 class="card-title">Lorem ipsum dolor sit am onse adipiscing elit</h3>
      <div class="card-meta"><span><b>Mara Kell</b> - Jul 23, 2016</span><span class="count">57</span></div>
      <div class="card-actions"><svg class="ico"><use href="#i-up"/></svg>22<span class="dislike"><svg class="ico"><use href="#i-down"/></svg>4</span><span class="dl"><svg class="ico"><use href="#i-dl"/></svg>Download</span></div></article>
    <article class="card"><div class="card-media" role="img" aria-label="Smiling woman listening to headphones in warm sunlight" style="background:linear-gradient(135deg,#f3d7b8,#e6a98a 50%,#c9443e)"><span class="play"></span></div>
      <h3 class="card-title">Lorem ipsum dolor sit am onse adipiscing elit</h3>
      <div class="card-meta"><span><b>Mara Kell</b> - Jul 23, 2016</span><span class="count">57</span></div>
      <div class="card-actions"><svg class="ico"><use href="#i-up"/></svg>22<span class="dislike"><svg class="ico"><use href="#i-down"/></svg>4</span><span class="dl"><svg class="ico"><use href="#i-dl"/></svg>Download</span></div></article>
    <article class="card"><div class="card-media" role="img" aria-label="Vintage microphone with golden bokeh lights" style="background:radial-gradient(circle at 70% 40%,#d9a64a,#3a2a14 70%)"><span class="play"></span></div>
      <h3 class="card-title">Lorem ipsum dolor sit am onse adipiscing elit</h3>
      <div class="card-meta"><span><b>Mara Kell</b> - Jul 23, 2016</span><span class="count">57</span></div>
      <div class="card-actions"><svg class="ico"><use href="#i-up"/></svg>22<span class="dislike"><svg class="ico"><use href="#i-down"/></svg>4</span><span class="dl"><svg class="ico"><use href="#i-dl"/></svg>Download</span></div></article>
  </div>
</section>

<div class="section-rule"></div>

<section class="media-section section-video">
  <div class="section-head"><h2>Latest Video’s</h2><a class="view-all" href="#">View All <svg class="ico" width="12" height="12"><use href="#i-circle-arrow"/></svg></a></div>
  <div class="grid">
    <article class="card"><div class="card-media" role="img" aria-label="Guitars and drum kit in a rehearsal room" style="background:linear-gradient(160deg,#5a6068,#2c3036 50%,#8a7a66)"><span class="play"></span></div>
      <h3 class="card-title">Lorem ipsum dolor sit am onse adipiscing elit</h3>
      <div class="card-meta"><span><b>Mara Kell</b> - Jul 23, 2016</span><span class="count">57</span></div>
      <div class="card-actions"><svg class="ico"><use href="#i-up"/></svg>22<span class="dislike"><svg class="ico"><use href="#i-down"/></svg>4</span><span class="dl"><svg class="ico"><use href="#i-dl"/></svg>Download</span></div></article>
    <article class="card"><div class="card-media" role="img" aria-label="Sheet music pages in black and white" style="background:linear-gradient(135deg,#e2e2e2,#9a9a9a 60%,#c8c8c8)"><span class="play"></span></div>
      <h3 class="card-title">Lorem ipsum dolor sit am onse adipiscing elit</h3>
      <div class="card-meta"><span><b>Mara Kell</b> - Jul 23, 2016</span><span class="count">57</span></div>
      <div class="card-actions"><svg class="ico"><use href="#i-up"/></svg>22<span class="dislike"><svg class="ico"><use href="#i-down"/></svg>4</span><span class="dl"><svg class="ico"><use href="#i-dl"/></svg>Download</span></div></article>
    <article class="card"><div class="card-media" role="img" aria-label="Concert audience with hands up in amber light" style="background:radial-gradient(circle at 50% 20%,#f1c27a,#a4621e 55%,#3a2210)"><span class="play"></span></div>
      <h3 class="card-title">Lorem ipsum dolor sit am onse adipiscing elit</h3>
      <div class="card-meta"><span><b>Mara Kell</b> - Jul 23, 2016</span><span class="count">57</span></div>
      <div class="card-actions"><svg class="ico"><use href="#i-up"/></svg>22<span class="dislike"><svg class="ico"><use href="#i-down"/></svg>4</span><span class="dl"><svg class="ico"><use href="#i-dl"/></svg>Download</span></div></article>
    <article class="card"><div class="card-media" role="img" aria-label="Cheering party crowd with colourful lights" style="background:linear-gradient(160deg,#d48a5a,#e9c9b0 40%,#6a3a4a)"><span class="play"></span></div>
      <h3 class="card-title">Lorem ipsum dolor sit am onse adipiscing elit</h3>
      <div class="card-meta"><span><b>Mara Kell</b> - Jul 23, 2016</span><span class="count">57</span></div>
      <div class="card-actions"><svg class="ico"><use href="#i-up"/></svg>22<span class="dislike"><svg class="ico"><use href="#i-down"/></svg>4</span><span class="dl"><svg class="ico"><use href="#i-dl"/></svg>Download</span></div></article>
    <article class="card"><div class="card-media" role="img" aria-label="Cowboy hat resting on an acoustic guitar" style="background:linear-gradient(150deg,#8a4a1e,#c9864a 45%,#2a1a10)"><span class="play"></span></div>
      <h3 class="card-title">Lorem ipsum dolor sit am onse adipiscing elit</h3>
      <div class="card-meta"><span><b>Mara Kell</b> - Jul 23, 2016</span><span class="count">57</span></div>
      <div class="card-actions"><svg class="ico"><use href="#i-up"/></svg>22<span class="dislike"><svg class="ico"><use href="#i-down"/></svg>4</span><span class="dl"><svg class="ico"><use href="#i-dl"/></svg>Download</span></div></article>
    <article class="card"><div class="card-media" role="img" aria-label="Man with headphones using a tablet outdoors" style="background:linear-gradient(160deg,#c9d2d8,#8a7a70 50%,#4a3a36)"><span class="play"></span></div>
      <h3 class="card-title">Lorem ipsum dolor sit am onse adipiscing elit</h3>
      <div class="card-meta"><span><b>Mara Kell</b> - Jul 23, 2016</span><span class="count">57</span></div>
      <div class="card-actions"><svg class="ico"><use href="#i-up"/></svg>22<span class="dislike"><svg class="ico"><use href="#i-down"/></svg>4</span><span class="dl"><svg class="ico"><use href="#i-dl"/></svg>Download</span></div></article>
  </div>
</section>

<aside class="sidebar">
  <div class="side-block subscribe">
    <h3 class="side-title">Subscribe for Updates</h3>
    <p class="side-text">Sign up to receive a copy of all new posts on this blog by email:</p>
    <div class="input-email"><svg class="ico"><use href="#i-mail"/></svg>Email</div>
    <div class="btn-send">Send me updates</div>
  </div>
  <ul class="side-block topics">
    <li><svg class="ico"><use href="#i-send"/></svg>How to Upload</li>
    <li><svg class="ico"><use href="#i-heart"/></svg>Procrastination</li>
    <li><svg class="ico"><use href="#i-up"/></svg>Be still</li>
    <li><svg class="ico"><use href="#i-down"/></svg>A brief guide to life</li>
    <li><svg class="ico"><use href="#i-globe"/></svg>The best goal is no goal</li>
    <li><svg class="ico"><use href="#i-globe"/></svg>The lost art of solitude</li>
  </ul>
  <div class="side-block gallery">
    <div class="thumb" role="img" aria-label="Studio microphone in front of a mixing desk" style="background:linear-gradient(135deg,#7a7a7a,#3a3a3a 60%,#a0a0a0)"></div>
    <p class="caption">users.</p>
    <div class="thumb-2" role="img" aria-label="Headphones close-up in soft light" style="background:linear-gradient(120deg,#1e4a6a,#d8d8a0 60%,#f1f0d8)"></div>
    <p class="caption">Because I didn't pay attention to users.</p>
    <div class="thumb-3" role="img" aria-label="Violin lying on a sunlit surface" style="background:linear-gradient(180deg,#e8e2d4,#c9a878 55%,#6a4a2a)"></div>
    <p class="caption">Because I didn't pay attention to users.</p>
  </div>
  <div class="side-block services">
    <h3 class="side-title">What We Do?</h3>
    <div class="service"><span class="svc-icon"><svg class="ico"><use href="#i-mouse"/></svg></span><p>If you are worried about something coming up, or caught up in.</p></div>
    <div class="service"><span class="svc-icon"><svg class="ico"><use href="#i-video"/></svg></span><p>If you are worried about something coming up, or caught up in.</p></div>
    <div class="service"><span class="svc-icon"><svg class="ico"><use href="#i-cart"/></svg></span><p>If you are worried about something coming up, or caught up in.</p></div>
  </div>
  <div class="side-block about">
    <h3 class="side-title">About Us</h3>
    <p>Listen to the world around you. Feel your breath coming in and going out. Listen to your thoughts. See the details of your surroundings. <a href="#">Read More...</a></p>
  </div>
</aside>

<footer class="site-footer">
  <div class="foot-col col-connect">
    <h3>LET'S CONNECT</h3>
    <div class="social">
      <a class="social-tile t-friends" href="#"><span class="dot">Friends</span><span class="num">2598</span></a>
      <a class="social-tile t-chirps" href="#"><span class="dot">Chirps</span><span class="num">4576</span></a>
      <a class="social-tile t-circles" href="#"><span class="dot">Circles</span><span class="num">1269</span></a>
    </div>
  </div>
  <div class="foot-divider" style="left:436px"></div>
  <div class="foot-col col-mail">
    <h3>MAILING LIST</h3>
    <p>Sign up for our mailing list to get latest updates and offers.</p>
    <div class="mail-form"><div class="mail-input">Email address</div><div class="mail-btn"><svg class="ico"><use href="#i-check"/></svg></div></div>
    <p class="privacy">We respect your privacy</p>
  </div>
  <div class="foot-divider" style="left:881px"></div>
  <div class="foot-col col-menu">
    <h3>MENU</h3>
    <ul class="foot-menu"><li>Home</li><li>About Us</li><li>Color</li><li>About</li><li>Contact</li></ul>
  </div>
  <p class="copyright">© COPYRIGHTS 2016 ALL RIGHTS RESERVED</p>
</footer>

</body>
</html>
```